ourTradeLoop Webdesign - trading your electronics for cash - helping you clear up clutter

We need web design (and an updated logo) for a new company based in London called "ourTradeLoop". It is a platform that enables users to sell their old electronics for cash, either for themselves or they can donate the cash to charity. In time, we also plan to enable buying of electronics on the site. We specialise in mobile phones, tablets, laptops, and games consoles. Please review brindlo.com, which is a US site with the same business, and also tunefernwick.co.uk, so have a similar business in the UK. We would like to see designs that use the colour red, and that are bold. We currently have a logo, and a WIP site built, but the design needs to be dramatically improved, the right colour mix needs to be chosen to give a clean and modern feel. Please review www.ourtradeloop.com to get an understanding of the work that needs to be improved.

Target Market(s)

People who buy electronics frequently, i.e. upgrade every time a new quince product comes out! These guys usually have a lap top, desk top, tablet and phone.

Industry/Entity Type

Electronics

Logo Text

ourTradeLoop

Number of Pages Required

3 page

Font styles to use
Sans Serif

Colors
ec1f27

Requirements
Must have
• Home page design
• "How-it-works" page design
• Sell page design
• Must use the colour red, and have a secondary/accent colour.

```html
<!DOCTYPE html>
<html lang="en">
<head>
<meta charset="utf-8">
<title>ourTradeLoop – Sell your electronics for cash</title>
<link href="https://fonts.googleapis.com/css2?family=Open+Sans:wght@300;400;600;700;800&display=swap" rel="stylesheet">
<style>
:root{
  --red:#ec1f27;
  --teal:#3ec7b3;
  --teal-dark:#2aa896;
  --orange:#f6a53c;
  --orange-dark:#ef8a2a;
  --green:#7cc242;
  --ink:#333;
  --mute:#888;
  --grey:#ececec;
  --grey-dark:#d9d9d9;
  --footer:#3b3b3b;
  --white:#fff;
}
*{box-sizing:border-box;margin:0;padding:0}
html,body{width:1200px;height:2332px;overflow:hidden}
body{font-family:"Open Sans",Arial,sans-serif;color:var(--ink);background:var(--white);position:relative}
.abs{position:absolute}

/* header */
.site-header{position:absolute;left:0;top:0;width:1200px;height:220px;background:var(--white)}
.brand-badge{position:absolute;left:535px;top:14px;width:130px;height:130px;border-radius:50%;background:var(--teal);border:6px solid #d8f3ef;display:flex;align-items:center;justify-content:center}
.brand-badge span{color:var(--white);font-weight:700;font-size:15px}
.account-links{position:absolute;right:60px;top:26px;display:flex;gap:18px;font-size:13px;font-weight:600;color:var(--ink)}
.account-links i{display:inline-block;width:10px;height:10px;background:var(--red);margin-right:6px;border-radius:2px}
.main-nav{position:absolute;top:156px;left:0;width:1200px;display:flex;justify-content:center;gap:14px}
.pill{height:40px;border-radius:20px;padding:0 22px;display:flex;align-items:center;gap:8px;font-size:14px;font-weight:700;color:var(--white)}
.pill .dot{width:18px;height:18px;border-radius:50%;background:rgba(255,255,255,.85)}
.pill.grey{background:#9a9a9a}
.pill.red{background:var(--red)}
.donate{position:absolute;right:70px;top:152px;background:var(--green);color:var(--white);font-weight:700;font-size:16px;padding:12px 26px}

/* hero */
.hero{position:absolute;left:0;top:220px;width:1200px;height:580px;overflow:hidden}
.hero-left{position:absolute;left:0;top:0;width:600px;height:580px;background:linear-gradient(160deg,#55d3c1,var(--teal-dark))}
.hero-right{position:absolute;left:600px;top:0;width:600px;height:580px;background:linear-gradient(200deg,#f9b64e,var(--orange-dark))}
.hero-banner{position:absolute;top:36px;left:0;width:1200px;display:flex;justify-content:center}
.hero-banner b{background:var(--red);color:var(--white);padding:8px 16px;font-size:22px;font-weight:800}
.hero-banner span{background:var(--white);color:var(--red);padding:8px 16px;font-size:22px;font-weight:700}
.hero-devices{position:absolute;left:420px;top:110px;width:360px;height:460px;background:linear-gradient(90deg,#e6e6e6,#2f3135 50%,#bfc3c9);border-radius:30px 30px 0 0}
.hero-person{position:absolute;top:170px;width:170px;height:400px;border-radius:80px 80px 0 0}
.hero-person.buyer{left:70px;background:linear-gradient(#6b4b35,#4b7a78)}
.hero-person.seller{left:960px;background:linear-gradient(#3b3b3b,#c25a22)}
.hero-word{position:absolute;top:400px;color:var(--white);font-weight:300;font-size:84px;line-height:1}
.hero-word small{display:block;font-size:13px;font-weight:700;letter-spacing:1px;margin-top:8px}
.hero-word.buy{left:240px}
.hero-word.sell{left:810px}
.hero-arrow{position:absolute;top:250px;width:40px;height:60px;background:rgba(0,0,0,.45);display:flex;align-items:center;justify-content:center}

/* bestsellers */
.bestsellers{position:absolute;left:0;top:800px;width:1200px;height:500px;background:var(--grey)}
.section-tab{position:absolute;left:60px;top:26px;background:var(--red);color:var(--white);font-weight:800;font-size:18px;padding:10px 20px}
.category-tabs{position:absolute;left:340px;top:28px;display:flex;gap:4px}
.category-tabs span{background:var(--grey-dark);font-size:14px;padding:10px 22px;color:#555}
.category-tabs span.active{background:var(--white);color:var(--ink);font-weight:600}
.see-all{position:absolute;right:60px;top:36px;font-size:13px;color:#555}
.product-panel{position:absolute;left:60px;top:70px;width:1080px;height:330px;background:var(--white);display:flex;gap:20px;padding:22px}
.product-card{flex:1;border:1px solid #e2e2e2;position:relative;padding:12px}
.product-tag{position:absolute;left:-4px;top:10px;background:#3a8fd0;color:var(--white);font-size:11px;font-weight:700;padding:3px 10px}
.product-photo{height:170px;margin:18px 30px 10px;border-radius:10px}
.product-name{font-size:13px;color:#555}
.product-from{font-size:11px;color:var(--mute)}
.product-price{font-size:22px;color:var(--red);font-weight:600}
.product-foot{display:flex;justify-content:space-between;align-items:center}
.stars{color:#f5a623;font-size:14px;letter-spacing:2px}
.sell-btn{background:var(--red);color:var(--white);font-size:11px;font-weight:700;padding:4px 10px}
.pager{position:absolute;left:0;top:432px;width:1200px;display:flex;justify-content:center;gap:16px}
.pager i{width:34px;height:34px;border-radius:50%;background:#bdbdbd;display:block}
.pager i.on{background:var(--red)}

/* stories */
.stories{position:absolute;left:0;top:1300px;width:1200px;height:460px}
.section-title{position:absolute;left:60px;top:44px;color:var(--red);font-size:26px;font-weight:600}
.story-arrows{position:absolute;right:60px;top:50px;display:flex;gap:8px}
.story-arrows i{width:24px;height:24px;border-radius:50%;border:2px solid var(--red);display:block}
.story-row{position:absolute;left:60px;top:110px;width:1080px;display:flex;gap:40px}
.story{flex:1}
.story-quote{background:#f1f1f1;padding:36px 30px;font-size:14px;line-height:1.6;color:#666;position:relative;text-align:center}
.story-quote:before{content:"\201C";position:absolute;left:14px;top:-6px;font-size:60px;color:#ccc}
.story-author{display:flex;align-items:center;gap:14px;margin:26px 0 0 70px}
.avatar{width:70px;height:70px;border-radius:50%;background:#c9c9c9}
.story-author b{display:block;font-size:16px}
.story-author span{font-size:12px;color:var(--mute)}

/* reasons */
.reasons{position:absolute;left:0;top:1760px;width:1200px;height:250px;background:var(--grey)}
.reasons-title{position:absolute;left:460px;top:-20px;width:280px;height:44px;border-radius:22px;background:#555;color:var(--white);font-weight:600;font-size:16px;display:flex;align-items:center;justify-content:center}
.reason-row{position:absolute;left:60px;top:60px;width:1080px;display:flex;gap:50px}
.reason{flex:1;display:flex;gap:14px}
.reason-icon{flex:0 0 40px;height:40px;border-radius:50%;background:var(--red);display:flex;align-items:center;justify-content:center}
.reason h3{font-size:16px;font-weight:700;margin-bottom:8px}
.reason p{font-size:13px;line-height:1.6;color:#666}
.reason p em{color:var(--red);font-style:normal}

/* footer */
.site-footer{position:absolute;left:0;top:2010px;width:1200px;height:250px;background:var(--footer);color:#ccc}
.footer-col{position:absolute;top:30px;font-size:13px;line-height:1.9}
.footer-col h4{color:var(--white);font-size:15px;font-weight:700;margin-bottom:8px}
.social i{display:inline-block;width:14px;height:14px;background:#777;border-radius:3px;margin-right:8px;vertical-align:middle}
.like-box{width:220px;height:110px;background:linear-gradient(#e8e8e8,#b8bcc4)}
.newsletter p{width:250px;line-height:1.5;font-size:12px;margin-bottom:10px}
.newsletter-form{display:flex}
.newsletter-form span{width:170px;height:32px;background:var(--white);color:#999;font-size:12px;padding:7px 10px}
.newsletter-form b{background:var(--red);color:var(--white);font-size:12px;padding:7px 14px}
.store-badges{position:absolute;left:60px;top:178px;display:flex;gap:16px}
.store-badges i{display:block;width:180px;height:54px;border-radius:8px;background:#111;border:1px solid #777}
.bottom-bar{position:absolute;left:0;top:2260px;width:1200px;height:72px;background:var(--white);display:flex;align-items:center;padding:0 60px}
.bottom-logo{display:flex;align-items:center;gap:8px;font-weight:700;color:var(--red);font-size:20px}
.bottom-logo i{width:20px;height:20px;background:var(--green);display:block}
.bottom-links{margin-left:auto;text-align:right;font-size:12px;color:#666;line-height:1.7}
</style>
</head>
<body>

<header class="site-header">
  <div class="brand-badge"><span>ourTradeLoop</span></div>
  <div class="account-links"><span><i></i>LOGIN</span><span><i></i>REGISTER</span></div>
  <nav class="main-nav">
    <span class="pill grey"><span class="dot"></span>HOW IT WORKS</span>
    <span class="pill red"><span class="dot"></span>BUY</span>
    <span class="pill red"><span class="dot"></span>SELL</span>
  </nav>
  <div class="donate">DONATE NOW</div>
</header>

<section class="hero">
  <div class="hero-left"></div>
  <div class="hero-right"></div>
  <div class="hero-banner"><b>GIVING NEW LIFE</b><span>TO USED SMARTPHONES &amp; OTHER DEVICES</span></div>
  <div class="hero-person buyer" role="img" aria-label="Illustrated buyer character"></div>
  <div class="hero-person seller" role="img" aria-label="Illustrated seller character"></div>
  <div class="hero-devices" role="img" aria-label="Two smartphones side by side"></div>
  <div class="hero-word buy">BUY<small>CERTIFIED ELECTRONICS</small></div>
  <div class="hero-word sell">SELL<small>CASH YOUR ELECTRONICS</small></div>
  <div class="hero-arrow" style="left:0"><svg width="16" height="24"><path d="M12 2 3 12l9 10" stroke="#fff" stroke-width="3" fill="none"/></svg></div>
  <div class="hero-arrow" style="right:0"><svg width="16" height="24"><path d="M4 2l9 10-9 10" stroke="#fff" stroke-width="3" fill="none"/></svg></div>
</section>

<section class="bestsellers">
  <div class="section-tab">BESTSELLERS</div>
  <div class="category-tabs"><span class="active">Mobile Phones</span><span>Tablets</span><span>Laptops</span><span>Games Consoles</span></div>
  <div class="see-all">See All Products ›</div>
  <div class="product-panel">
    <div class="product-card"><span class="product-tag">NORVIK</span>
      <div class="product-photo" role="img" aria-label="Norvik phone" style="background:linear-gradient(#3a3a3a,#8a6a55)"></div>
      <div class="product-name">Norvik</div><div class="product-from">From</div>
      <div class="product-foot"><span class="product-price">£349.00</span><span class="sell-btn">SELL IT</span></div>
      <div class="stars">★★★★☆</div></div>
    <div class="product-card"><span class="product-tag">QUINCE</span>
      <div class="product-photo" role="img" aria-label="Pomelo 5C phone" style="background:linear-gradient(#ffffff,#f3d25a)"></div>
      <div class="product-name">Pomelo 5C</div><div class="product-from">From</div>
      <div class="product-foot"><span class="product-price">£120.00</span><span class="sell-btn">SELL IT</span></div>
      <div class="stars">★★★★☆</div></div>
    <div class="product-card"><span class="product-tag">HALDEN</span>
      <div class="product-photo" role="img" aria-label="Halden phone" style="background:linear-gradient(#d0d0d0,#6d8aa8)"></div>
      <div class="product-name">Halden</div><div class="product-from">From</div>
      <div class="product-foot"><span class="product-price">£349.00</span><span class="sell-btn">SELL IT</span></div>
      <div class="stars">★★★★☆</div></div>
    <div class="product-card"><span class="product-tag">LUMEO</span>
      <div class="product-photo" role="img" aria-label="Lumeo 940XL phone" style="background:linear-gradient(#222,#3c7ac0)"></div>
      <div class="product-name">Lumeo 940XL</div><div class="product-from">From</div>
      <div class="product-foot"><span class="product-price">£210.00</span><span class="sell-btn">SELL IT</span></div>
      <div class="stars">★★★★☆</div></div>
  </div>
  <div class="pager"><i></i><i class="on"></i></div>
</section>

<section class="stories">
  <h2 class="section-title">CUSTOMER STORIES</h2>
  <div class="story-arrows"><i></i><i></i></div>
  <div class="story-row">
    <div class="story">
      <p class="story-quote">Selling my old phone took minutes. The price was fair, the free postage pack arrived next day and the cash landed in my account quickly. I will be back.</p>
      <div class="story-author"><div class="avatar"></div><div><b>Sam Rowan</b><span>Happy Seller</span></div></div>
    </div>
    <div class="story">
      <p class="story-quote">Selling my old phone took minutes. The price was fair, the free postage pack arrived next day and the cash landed in my account quickly. I will be back.</p>
      <div class="story-author"><div class="avatar"></div><div><b>Sam Rowan</b><span>Happy Seller</span></div></div>
    </div>
    <div class="story">
      <p class="story-quote">Selling my old phone took minutes. The price was fair, the free postage pack arrived next day and the cash landed in my account quickly. I will be back.</p>
      <div class="story-author"><div class="avatar"></div><div><b>Sam Rowan</b><span>Happy Seller</span></div></div>
    </div>
  </div>
</section>

<section class="reasons">
  <div class="reasons-title">Why Customers Choose Us</div>
  <div class="reason-row">
    <div class="reason"><div class="reason-icon"><svg width="20" height="14"><path d="M1 1h12v9H1zM13 4h4l2 3v3h-6" fill="#fff"/></svg></div>
      <div><h3>Fast &amp; Free Delivery</h3><p>Our standard delivery service is FREE in the UK, wherever you are. We send your pack within one day, <em>find out more</em>.</p></div></div>
    <div class="reason"><div class="reason-icon"><svg width="16" height="18"><path d="M3 8V5a5 5 0 0 1 10 0v3h2v10H1V8z" fill="#fff"/></svg></div>
      <div><h3>Safe &amp; Secure Payment</h3><p>Every payment is protected from start to finish, by bank transfer or cheque, <em>see how we keep it safe</em>.</p></div></div>
    <div class="reason"><div class="reason-icon"><svg width="18" height="14"><path d="M1 7l5 5L17 1" stroke="#fff" stroke-width="3" fill="none"/></svg></div>
      <div><h3>100% Money-back Guaranteed</h3><p>If you are not satisfied with your order we refund it in full, no questions asked, <em>read our guarantee</em>.</p></div></div>
  </div>
</section>

<footer class="site-footer">
  <div class="footer-col" style="left:60px"><h4>Let Us Help You</h4>Customer Service<br>Contact Us<br>Returns &amp; Exchanges<br>FAQs</div>
  <div class="footer-col social" style="left:270px"><h4>Follow Us</h4><i></i>Friendwall<br><i></i>Chirper<br><i></i>RSS</div>
  <div class="footer-col" style="left:450px"><h4>Get in Touch</h4>info@ourtradeloop.com<br>Contact Form</div>
  <div class="footer-col" style="left:660px"><h4>Like Us on Friendwall</h4><div class="like-box" role="img" aria-label="Social page preview"></div></div>
  <div class="footer-col newsletter" style="left:900px"><h4>Sign up to our newsletter</h4><p>Get our latest trade-in prices and offers sent to your inbox each week.</p>
    <div class="newsletter-form"><span>Enter email address</span><b>Sign Up</b></div></div>
  <div class="store-badges"><i></i><i></i></div>
</footer>

<div class="bottom-bar">
  <div class="bottom-logo"><i></i>ourTradeLoop</div>
  <div class="bottom-links">Legal • Site Terms • Service Terms • Privacy Policy • Law Enforcement<br>© 2016 ourTradeLoop Ltd. All Rights Reserved</div>
</div>

</body>
</html>
```